Zestora - Landing Page

Need a landing page for a journal app. The app is based on a retrospective board, where each journal entry is split into 3 sections: "What went well", "What Didn't Go Well" and "Things To Try".
The landing page should match the style of all modern web application landing pages. Think Brint, Tivalo, Mirvane. I've included screenshots of the app.
One feature that I want to highlight that is not ready yet, is an AI coach. It will offer insights based on the history of the user's journal entries
1 page

```html
<!DOCTYPE html>
<html lang="en">
<head>
<meta charset="utf-8">
<title>Zestora – Journal app landing page</title>
<link rel="stylesheet" href="https://fonts.googleapis.com/css2?family=Outfit:wght@400;500;600;700&family=Inter:wght@400;500;600;700&display=swap">
<style>
:root{
  --blue:#0b49ad;
  --blue-dark:#083c92;
  --ink:#1b1f2a;
  --body:#5b6272;
  --muted:#8a91a0;
  --light:#eef3fa;
  --line:#dfe4ec;
  --sidebar:#20283a;
  --green:#3db465;
  --star:#f5a623;
  --white:#ffffff;
}
*{box-sizing:border-box;margin:0;padding:0}
html,body{width:1200px;height:4435px;overflow:hidden}
body{position:relative;font-family:"Inter",sans-serif;color:var(--ink);background:var(--white)}
a{color:inherit;text-decoration:none}
.abs{position:absolute}
.display{font-family:"Outfit",sans-serif}

/* ---------- Header / hero ---------- */
.hero-band{left:0;top:0;width:1200px;height:620px;background:linear-gradient(180deg,#0b4ab0 0%,#0a45a6 100%)}
.light-band{left:0;top:620px;width:1200px;height:1722px;background:linear-gradient(150deg,#f4f7fc 0%,#e9eff8 45%,#f2f6fb 60%,#e6edf7 100%)}
.brand{font-family:"Outfit",sans-serif;font-weight:700;color:var(--white)}
.nav-brand{left:110px;top:18px;font-size:25px}
.nav{left:432px;top:26px;display:flex;gap:30px;font-size:15px;color:var(--white)}
.nav a.active{position:relative}
.nav a.active::before{content:"";position:absolute;left:0;right:0;top:-26px;height:4px;background:var(--white);border-radius:0 0 3px 3px}
.login{left:838px;top:26px;color:var(--white);font-size:15px;display:flex;align-items:center;gap:6px}
.btn{display:inline-flex;align-items:center;justify-content:center;border-radius:30px;font-size:15px;font-weight:500}
.btn-white{background:var(--white);color:var(--blue)}
.btn-outline{border:2px solid var(--white);color:var(--white)}
.btn-blue{background:var(--blue);color:var(--white)}
.nav-cta{left:937px;top:18px;width:151px;height:42px}
.hero-title{left:0;width:1200px;top:145px;text-align:center;color:var(--white);font-family:"Outfit",sans-serif;font-size:40px;line-height:52px}
.hero-title b{font-weight:700;display:block}
.hero-title span{font-weight:400;display:block}
.hero-btns{left:0;width:1200px;top:259px;display:flex;justify-content:center;gap:12px}
.hero-btns .btn{width:150px;height:40px}
.round-arrow{width:46px;height:46px;border-radius:50%;background:rgba(255,255,255,.14);display:flex;align-items:center;justify-content:center}

/* ---------- Device mockup ---------- */
.device{background:var(--white);border:7px solid #eef1f6;border-radius:24px;box-shadow:0 18px 40px rgba(20,40,90,.18);overflow:hidden;display:flex}
.device .rail{width:34px;background:var(--sidebar);display:flex;flex-direction:column;align-items:center;padding-top:10px;gap:10px;position:relative}
.rail i{display:block;width:12px;height:9px;border-radius:2px;background:#cfd6e2}
.rail i.logo{background:var(--green);height:12px}
.rail .avatar{position:absolute;bottom:8px;width:14px;height:14px;border-radius:50%;background:#cfd6e2}
.screen{flex:1;padding:14px 20px;position:relative}
.entry-title{font-size:13px;font-weight:700}
.entry-meta{display:flex;align-items:center;gap:8px;font-size:8px;margin-top:8px}
.pill{background:var(--green);color:var(--white);border-radius:10px;padding:2px 7px;font-size:7px}
.pill.dark{background:#2d3748}
.col{flex:1;border:1px solid var(--line);border-radius:4px;padding:8px}
.col-head{font-size:8px;display:flex;gap:6px;align-items:center;color:#333}
.col-head i{width:8px;height:8px;border-radius:2px;background:#4a76d6;display:inline-block}
.editor{border:1px solid var(--line);margin-top:12px;height:calc(100% - 24px);display:flex;flex-direction:column}
.toolbar{font-size:7px;color:#555;padding:5px 7px;border-bottom:1px solid var(--line);line-height:11px}
.editor ul{font-size:8.6px;line-height:13.5px;padding:10px 10px 0 24px;color:#333}

/* ---------- Feature sections ---------- */
.accent{background:var(--blue);border-radius:16px}
.feature-title{font-family:"Outfit",sans-serif;font-size:43px;line-height:51px;color:var(--ink);font-weight:400}
.feature-title b{font-weight:700}
.feature-title span{font-weight:400}
.feature-text{font-size:14.2px;line-height:25.7px;color:var(--body)}
.more{font-size:14.5px;font-weight:600;color:var(--blue-dark);text-decoration:underline;text-underline-offset:3px;display:flex;align-items:center;gap:4px}

/* list view */
.list-card{border:1px solid var(--line);margin:0 10px;padding:12px;font-size:7.5px;line-height:11px;color:#333}
.list-card h5{font-size:9px;margin-bottom:2px}
.list-card .sub{color:var(--muted)}

/* dashboard */
.dash{background:#fbfcfe}
.dash .side{width:78px;padding:14px 8px;font-size:6.5px;color:#555;display:flex;flex-direction:column;gap:12px;border-right:1px solid #eef0f4}
.dash .side .on{background:var(--sidebar);color:var(--white);padding:5px 6px;border-radius:3px}
.dcard{position:absolute;background:var(--white);border-radius:8px;box-shadow:0 4px 14px rgba(30,50,90,.08);padding:10px;font-size:7px;color:#333}
.dcard h6{font-size:7.5px;font-weight:600}
.bars{display:inline-flex;gap:2px;align-items:flex-end;height:22px}
.bars i{width:4px;background:var(--green);border-radius:1px}
.prog{height:3px;background:#e5e8ee;border-radius:2px;margin:4px 0 9px}
.prog i{display:block;height:100%;border-radius:2px}

/* ---------- Testimonials ---------- */
.section-title{left:0;width:1200px;text-align:center;font-family:"Outfit",sans-serif;font-size:41px;color:var(--ink);font-weight:400}
.section-title b{font-weight:700}
.video{left:112px;top:2518px;width:487px;height:318px;background:linear-gradient(135deg,#6e6a66 0%,#b3aca3 40%,#8a8178 70%,#3e3c3b 100%)}
.play{left:310px;top:2651px;width:90px;height:52px;background:var(--blue);display:flex;align-items:center;justify-content:center}
.stars{color:var(--star);letter-spacing:3px}
.quote{left:647px;top:2568px;width:440px;font-size:20.4px;line-height:30px;font-style:italic;color:#3b4150}

/* ---------- Deep dive ---------- */
.dive-band{left:0;top:2988px;width:1200px;height:671px;background:var(--light)}
.card{background:var(--white);border:1px solid #d9dfe8;border-radius:4px;padding:15px}
.card .thumb{width:100%;height:222px;border-radius:3px}
.card h4{font-family:"Outfit",sans-serif;font-weight:500;font-size:25px;line-height:34px;margin:24px 4px 0}
.card .more{margin:22px 4px 0}
.dots{left:552px;top:3574px;display:grid;grid-template-columns:repeat(11,8px);gap:4px}
.dots i{width:2px;height:2px;background:#444;border-radius:50%}

/* ---------- CTA ---------- */
.cta-title{left:0;width:1200px;top:3730px;text-align:center;font-family:"Outfit",sans-serif;font-size:43px;line-height:52px;font-weight:400}
.cta-title b{font-weight:700;display:block}
.cta-title span{font-weight:400;display:block}

/* ---------- Footer ---------- */
.footer{left:0;top:4012px;width:1200px;height:423px;background:var(--blue)}
.foot-brand{left:126px;top:4098px;font-size:33px}
.foot-text{left:126px;top:4160px;width:290px;font-size:15px;line-height:26px;color:var(--white)}
.social{left:126px;top:4232px;display:flex;gap:14px;font-size:12px;color:var(--white)}
.col-title{font-family:"Outfit",sans-serif;font-weight:600;font-size:21px;color:var(--white)}
.foot-links{display:flex;flex-direction:column;gap:6px;font-size:15px;color:var(--white);line-height:20px}
.legal{top:4380px;font-size:15px;color:var(--white)}
</style>
</head>
<body>

<!-- Hero -->
<div class="abs hero-band"></div>
<div class="abs light-band"></div>

<div class="abs brand nav-brand">Zestora</div>
<nav class="abs nav">
  <a class="active" href="#">Home</a><a href="#">Products</a><a href="#">Solutions</a><a href="#">Resources</a>
</nav>
<a class="abs login" href="#">
  <svg width="16" height="16" viewBox="0 0 16 16" fill="none" stroke="#fff" stroke-width="1.5"><circle cx="8" cy="5" r="3"/><path d="M2 15c0-3.3 2.7-5 6-5s6 1.7 6 5"/></svg>Login
</a>
<a class="abs btn btn-white nav-cta" href="#">Get Started</a>

<h1 class="abs hero-title"><b>Made for people.</b><span>Built for productivity</span></h1>
<div class="abs hero-btns">
  <a class="btn btn-white" href="#">Get Started</a>
  <a class="btn btn-outline" href="#">Find Your Plan</a>
</div>
<div class="abs round-arrow" style="left:66px;top:287px"><svg width="10" height="10" viewBox="0 0 10 10"><path d="M6.5 1.5L3 5l3.5 3.5" stroke="#fff" stroke-width="1.5" fill="none"/></svg></div>
<div class="abs round-arrow" style="left:1088px;top:287px"><svg width="10" height="10" viewBox="0 0 10 10"><path d="M3.5 1.5L7 5 3.5 8.5" stroke="#fff" stroke-width="1.5" fill="none"/></svg></div>

<div class="abs device" style="left:203px;top:329px;width:796px;height:458px">
  <div class="rail"><i class="logo"></i><i></i><i></i><i></i><span class="avatar"></span></div>
  <div class="screen">
    <div class="entry-title" style="margin-left:38px">Entry</div>
    <div class="entry-meta" style="margin-left:38px">Thu Aug 22 2024 ⌄ <span class="pill">Gym</span></div>
    <div style="display:flex;height:348px;margin:24px 0 0 38px;gap:26px">
      <div class="col"><div class="col-head"><i></i>What Went Well?</div><div class="editor"><div class="toolbar">Normal ⇕ &nbsp;B I U S ”<br>≡ ≡ ≡ ≡ &nbsp;Tx</div>
        <ul><li>Completed all scheduled workouts this week.</li><li>Increased bench press weight by 10 pounds.</li><li>Maintained consistent energy levels throughout sessions.</li></ul></div></div>
      <div class="col"><div class="col-head"><i style="background:#6d7fd8"></i>What Didn't Go Well?</div><div class="editor"><div class="toolbar">Normal ⇕ &nbsp;B I U S ”<br>≡ ≡ ≡ ≡ &nbsp;Tx</div>
        <ul><li>Struggled with form on deadlifts, leading to lower back discomfort.</li><li>Missed two stretching sessions after workouts.</li><li>Skipped meal prep, resulting in inconsistent nutrition.</li></ul></div></div>
      <div class="col"><div class="col-head"><i style="background:#8a96b8"></i>Things To Try</div><div class="editor"><div class="toolbar">Normal ⇕ &nbsp;B I U S ”<br>≡ ≡ ≡ ≡ &nbsp;Tx</div>
        <ul><li>Focus on deadlift form by lowering the weight and reviewing proper technique.</li><li>Set reminders for post-workout stretching to prevent muscle tightness.</li><li>Dedicate Sunday evenings to meal prep to ensure a balanced diet.</li></ul></div></div>
    </div>
  </div>
</div>

<!-- Feature 1 -->
<div class="abs accent" style="left:1024px;top:843px;width:86px;height:120px"></div>
<h2 class="abs feature-title" style="left:112px;top:906px"><b>The fastest way to get</b><br><span>tasks out of your head.</span></h2>
<p class="abs feature-text" style="left:112px;top:1016px;width:440px">Lorem ipsum dolor sit amet, consectetur adipiscing elit, sed do eiusmod tempor incididunt ut labore et dolore magna aliqua. Ut enim ad minim veniam, quis nostrud exercitation ullamco laboris nisi ut aliquip ex ea commodo consequat. Duis aute irure dolor in reprehenderit in voluptate velit esse cillum dolore eu fugiat nulla pariatur. Excepteur sint occaecat cupidatat</p>
<a class="abs more" style="left:112px;top:1186px" href="#">Find Out More <svg width="16" height="8" viewBox="0 0 16 8"><path d="M0 4h14M11 1l3 3-3 3" stroke="currentColor" stroke-width="1.5" fill="none"/></svg></a>

<div class="abs device" style="left:598px;top:866px;width:495px;height:381px">
  <div class="rail"><i class="logo"></i><i></i><i></i><i></i><span class="avatar"></span></div>
  <div class="screen" style="padding:8px 0 0 52px">
    <div class="entry-title" style="font-size:11px">Entry</div>
    <div class="entry-meta" style="font-size:7px">Wed Aug 21 2024 ⌄ <span class="pill dark">Default Journal</span></div>
    <div style="display:flex;gap:14px;margin-top:16px;height:290px">
      <div class="col" style="flex:0 0 170px"><div class="col-head" style="font-size:6.5px"><i></i>What Went Well?</div><div class="editor"><div class="toolbar" style="font-size:6px">Normal ⇕ B I U S ”<br>≡ ≡ ≡ ≡ Tx</div></div></div>
      <div class="col" style="flex:0 0 170px"><div class="col-head" style="font-size:6.5px"><i></i>What Didn't Go Well?</div><div class="editor"><div class="toolbar" style="font-size:6px">Normal ⇕ B I U S ”<br>≡ ≡ ≡ ≡ Tx</div></div></div>
      <div class="col" style="flex:0 0 60px;border-right:none"><div class="col-head" style="font-size:6.5px"><i></i></div><div class="editor" style="border-right:none"><div class="toolbar" style="font-size:6px">Nor<br>≡ ≡</div></div></div>
    </div>
  </div>
</div>

<!-- Feature 2 -->
<div class="abs accent" style="left:90px;top:1319px;width:88px;height:120px"></div>
<div class="abs device" style="left:108px;top:1341px;width:498px;height:378px">
  <div class="rail"><i class="logo"></i><i></i><i></i><i></i><span class="avatar"></span></div>
  <div class="screen" style="padding:18px 0 0 52px">
    <div style="display:inline-block;border:1px solid var(--line);border-radius:3px;font-size:6.5px;padding:3px 7px;margin-left:27px">+ Add New</div>
    <div class="list-card" style="margin:14px 10px 0 27px;height:250px">
      <h5>Thu Aug 22 2024</h5>
      <div class="sub">What Went Well</div>
      Completed all scheduled workouts this week.<br>Increased bench press weight by 10 pounds.<br>Maintained consistent energy levels throughout sessions.
      <div class="sub">What Didn't Go Well</div>
      Struggled with form on deadlifts, leading to lower back discomfort.<br>Missed two stretching sessions after workouts.<br>Skipped meal prep, resulting in inconsistent nutrition.
      <div class="sub">Things To Try</div>
      Focus on deadlift form by lowering the weight and reviewing proper technique.<br>Set reminders for post-workout stretching to prevent muscle tightness.<br>Dedicate Sunday evenings to meal prep to ensure a balanced diet.
    </div>
    <div class="list-card" style="margin:6px 10px 0 27px;border-bottom:none">
      <h5>Tue Aug 20 2024</h5><div class="sub">What Went Well</div>Achieved a personal best in squats, adding 15 pounds.
    </div>
  </div>
</div>
<h2 class="abs feature-title" style="left:646px;top:1352px"><b>Reach that mental</b><br><span>clarity you’ve been<br>longing for.</span></h2>
<p class="abs feature-text" style="left:646px;top:1512px;width:442px">Lorem ipsum dolor sit amet, consectetur adipiscing elit, sed do eiusmod tempor incididunt ut labore et dolore magna aliqua. Ut enim ad minim veniam, quis nostrud exercitation ullamco laboris nisi ut aliquip ex ea commodo consequat. Duis aute irure dolor in reprehenderit in voluptate velit esse cillum dolore eu fugiat nulla pariatur.</p>
<a class="abs more" style="left:646px;top:1677px" href="#">Find Out More <svg width="16" height="8" viewBox="0 0 16 8"><path d="M0 4h14M11 1l3 3-3 3" stroke="currentColor" stroke-width="1.5" fill="none"/></svg></a>

<!-- Feature 3: AI Coach -->
<h2 class="abs feature-title" style="left:112px;top:1870px"><b>AI</b> <span>Coach</span></h2>
<p class="abs feature-text" style="left:112px;top:1937px;width:440px">Lorem ipsum dolor sit amet, consectetur adipiscing elit, sed do eiusmod tempor incididunt ut labore et dolore magna aliqua. Ut enim ad minim veniam, quis nostrud exercitation ullamco laboris nisi ut aliquip ex ea commodo consequat. Duis aute irure dolor in reprehenderit in voluptate velit esse cillum dolore eu fugiat nulla pariatur. Excepteur sint occaecat cupidatat</p>
<a class="abs more" style="left:112px;top:2110px" href="#">Find Out More <svg width="16" height="8" viewBox="0 0 16 8"><path d="M0 4h14M11 1l3 3-3 3" stroke="currentColor" stroke-width="1.5" fill="none"/></svg></a>

<div class="abs accent" style="left:1033px;top:2066px;width:81px;height:152px"></div>
<div class="abs device dash" style="left:598px;top:1818px;width:492px;height:379px">
  <div class="side">
    <b style="font-size:8px;color:#222">Dashboard</b><span>Project</span><span class="on">Statistics</span><span>Media</span><span>Dashboard</span><span>Reports</span>
    <span style="margin-top:auto">Settings</span>
  </div>
  <div style="position:absolute;left:104px;top:14px;display:flex;gap:6px;align-items:center;font-size:8px"><i style="width:22px;height:22px;border-radius:50%;background:#dfe3ea;display:inline-block"></i><span><b>User Name</b><br><span style="font-size:6px;color:#999">Lorem ipsum</span></span></div>
  <div class="dcard" style="left:104px;top:78px;width:96px;height:140px"><h6>Category name</h6>
    <div style="margin-top:14px">JAN<br><b style="font-size:12px">12k</b> <span class="bars"><i style="height:9px"></i><i style="height:14px"></i><i style="height:19px"></i><i style="height:12px"></i></span></div>
    <div style="margin-top:12px">FEB<br><b style="font-size:12px">1.2m</b> <span class="bars"><i style="height:11px"></i><i style="height:18px"></i><i style="height:14px"></i><i style="height:20px"></i></span></div></div>
  <div class="dcard" style="left:208px;top:78px;width:96px;height:140px"><h6>Category</h6><b style="font-size:17px;display:block;margin-top:14px">1282</b><span style="color:#999">+136</span>
    <svg width="78" height="40" viewBox="0 0 78 40" style="margin-top:10px"><path d="M2 30 Q12 10 20 24 T38 20 T56 14 T76 8" stroke="#3db465" stroke-width="1.6" fill="none"/></svg></div>
  <div class="dcard" style="left:104px;top:224px;width:200px;height:110px"><h6>Category name</h6>
    <table style="width:100%;font-size:5.5px;margin-top:10px;border-collapse:collapse;line-height:15px"><tr><td>Lorem ipsum</td><td>18/02/2021</td><td style="color:#3db465">$300</td><td>$300</td></tr><tr><td>Dolor</td><td>18/02/2021</td><td style="color:#3db465">$120</td><td>$172</td></tr><tr><td>Sit amet</td><td>18/02/2021</td><td style="color:#3db465">$15</td><td>$456</td></tr></table></div>
  <div class="dcard" style="left:346px;top:78px;width:122px;height:60px;background:#23272f;color:#fff"><span style="font-size:5.5px">Progress</span><b style="display:block;font-size:12px">4751</b><div class="prog" style="background:#555"><i style="width:72%;background:var(--green)"></i></div></div>
  <div class="dcard" style="left:346px;top:148px;width:122px;height:186px;box-shadow:none;background:transparent"><h6>Category name</h6>
    <div style="margin-top:14px">Lorem ipsum <b style="float:right">40%</b></div><div class="prog"><i style="width:40%;background:#333"></i></div>
    <div>Dolor <b style="float:right">35%</b></div><div class="prog"><i style="width:35%;background:var(--green)"></i></div>
    <div>Sit amet <b style="float:right">15%</b></div><div class="prog"><i style="width:15%;background:#4a76d6"></i></div>
    <div>Consectetur <b style="float:right">10%</b></div><div class="prog"><i style="width:10%;background:#333"></i></div></div>
</div>

<!-- Testimonials -->
<h2 class="abs section-title" style="top:2440px"><b>Testimonials</b></h2>
<div class="abs video" role="img" aria-label="Photo of a team looking at a tablet together in an office"></div>
<div class="abs play"><svg width="20" height="22" viewBox="0 0 20 22"><path d="M2 1l17 10L2 21z" fill="#fff"/></svg></div>
<div class="abs stars" style="left:647px;top:2532px;font-size:17px">★★★★★</div>
<p class="abs quote">“Lorem ipsum dolor sit amet, consectetur adipi scing elit, sed do eiusmod tempor incidid unt ut labore et dolore magna aliqua. Ut enim ad min im veniam, quis nostrud exercita tion ullamco laboris nisi ut aliquip ex dolore eu fugiat nulla pariatur.”</p>
<div class="abs display" style="left:647px;top:2763px;font-size:24px;font-weight:600">John Doe</div>
<div class="abs" style="left:647px;top:2799px;font-size:15px;color:var(--body)">Company name</div>
<a class="abs btn btn-blue" style="left:474px;top:2867px;width:253px;height:40px" href="#">See more customer stories</a>

<!-- Deep dive -->
<div class="abs dive-band"></div>
<h2 class="abs section-title" style="top:3052px"><b>Take a deeper dive into</b> a new way to work</h2>
<div class="abs" style="left:46px;top:3330px"><svg width="14" height="20" viewBox="0 0 14 20"><path d="M10 2L3 10l7 8" stroke="#222" stroke-width="2" fill="none"/></svg></div>
<div class="abs" style="left:1136px;top:3330px"><svg width="14" height="20" viewBox="0 0 14 20"><path d="M4 2l7 8-7 8" stroke="#222" stroke-width="2" fill="none"/></svg></div>

<article class="abs card" style="left:112px;top:3131px;width:303px;height:399px">
  <div class="thumb" role="img" aria-label="Illustration of a laptop with floating marketing and media icons" style="background:linear-gradient(135deg,#3a4f72 0%,#8b9ab3 45%,#c94040 100%)"></div>
  <h4>Lorem ipsum dolor sit amet, consectetur</h4>
  <a class="more" href="#">Find Out More <svg width="16" height="8" viewBox="0 0 16 8"><path d="M0 4h14M11 1l3 3-3 3" stroke="currentColor" stroke-width="1.5" fill="none"/></svg></a>
</article>
<article class="abs card" style="left:436px;top:3131px;width:329px;height:430px;box-shadow:0 8px 24px rgba(30,50,90,.12)">
  <div class="thumb" role="img" aria-label="Illustration of a phone in a hand surrounded by app icons" style="height:246px;background:linear-gradient(135deg,#1f2a3d 0%,#3d6ea8 50%,#d28a3a 100%)"></div>
  <h4>Lorem ipsum dolor sit amet, consectetur</h4>
  <a class="more" href="#">Find Out More <svg width="16" height="8" viewBox="0 0 16 8"><path d="M0 4h14M11 1l3 3-3 3" stroke="currentColor" stroke-width="1.5" fill="none"/></svg></a>
</article>
<article class="abs card" style="left:785px;top:3131px;width:303px;height:399px">
  <div class="thumb" role="img" aria-label="Illustration of a laptop with a glowing network of technology icons" style="background:linear-gradient(135deg,#2b3a2d 0%,#6f7d5a 45%,#b9a77a 100%)"></div>
  <h4>Lorem ipsum dolor sit amet, consectetur</h4>
  <a class="more" href="#">Find Out More <svg width="16" height="8" viewBox="0 0 16 8"><path d="M0 4h14M11 1l3 3-3 3" stroke="currentColor" stroke-width="1.5" fill="none"/></svg></a>
</article>
<div class="abs dots"><i></i><i></i><i></i><i></i><i></i><i></i><i></i><i></i><i></i><i></i><i></i><i></i><i></i><i></i><i></i><i></i><i></i><i></i><i></i><i></i><i></i><i></i><i></i><i></i><i></i><i></i><i></i><i></i><i></i><i></i><i></i><i></i><i></i></div>

<!-- CTA -->
<h2 class="abs cta-title"><b>Gain calmness and clarity with the world’s</b><span>most beloved productivity app</span></h2>
<div class="abs" style="left:0;width:1200px;top:3853px;text-align:center;font-size:15px">374000+ <span class="stars" style="font-size:14px;letter-spacing:1px">★★★★★</span> reviews on Playhub and Appvault</div>
<a class="abs btn btn-blue" style="left:529px;top:3890px;width:149px;height:40px" href="#">Start for free</a>

<!-- Footer -->
<footer>
<div class="abs footer"></div>
<div class="abs brand foot-brand">Zestora</div>
<p class="abs foot-text">Join millions of people who organize work and life with Zestora.</p>
<div class="abs social"><a href="#">Frendo</a><a href="#">Pictly</a><a href="#">Linkwise</a><a href="#">Vidora</a></div>

<div class="abs col-title" style="left:482px;top:4102px">Features</div>
<div class="abs foot-links" style="left:482px;top:4162px"><a href="#">How It Works</a><a href="#">For Teams</a><a href="#">Pricing</a><a href="#">Templates</a></div>
<div class="abs col-title" style="left:697px;top:4102px">Resources</div>
<div class="abs foot-links" style="left:697px;top:4162px"><a href="#">Download Apps</a><a href="#">Help Center</a><a href="#">Productivity Methods</a><a href="#">Integrations</a><a href="#">Channel Partners</a><a href="#">Developer API</a><a href="#">Status</a></div>
<div class="abs col-title" style="left:945px;top:4102px">Company</div>
<div class="abs foot-links" style="left:945px;top:4162px"><a href="#">About Us</a><a href="#">Careers</a><a href="#">Inspiration Hub</a><a href="#">Press</a><a href="#">Threadly</a></div>

<div class="abs legal" style="left:126px">Security &nbsp;| &nbsp;Privacy &nbsp;| &nbsp;Terms</div>
<div class="abs legal" style="left:771px">© Copyrights 2024 | All Rights Reserved</div>
</footer>

</body>
</html>
```